Celvara Health Group Presentation Folder, for Cancer Awareness, VERY COLORFUL AND MODERN

Presentation Folder I know pretty much what i want so it should be very eazy , I have included files from folders I use now rebrand them to my new company they will be fine, no sense re creating the wheel
Full Bleed Size
20.87" x 16.68"
53 x 42.4 cm
6260 x 5004 pixels
Document Trim Size
20.75" x 16.56"
52.7 x 42.1 cm
6225 x 4969 pixels

Low design quality

Industry/Entity Type

Medical

Font styles to use
Serif

Colors

Designer to choose colors to be used in the design.

Requirements
Must have
• really I am not looking for some one to redesign, we like our folder front page and would like to see new word information added., there are two folder front pages to choose from
• So Keep the original front page and redesign the back page and the pockets
• Can Make your Design off of one of the ones I already uploaded
Nice to have
• Keep the same color schemes, Keep the original front page and redesign the back page and the pockets
Should not have
• DO not recreate the front covers, use what I gave you and just rebrand

```html
<!DOCTYPE html>
<html lang="en">
<head>
<meta charset="utf-8">
<title>Celvara Health Group – Presentation Folder</title>
<link href="https://fonts.googleapis.com/css2?family=Raleway:wght@400;500;600;700&display=swap" rel="stylesheet">
<style>
:root{
  --pink:#f294a6;
  --pink-light:#f7c3cd;
  --red:#e8393a;
  --gene-red:#e0313a;
  --grey:#7d7d7d;
  --grey-light:#d9d9d9;
  --row-alt:#e8e8e8;
  --yellow:#f9c233;
  --orange-row:#fbd68a;
  --lime:#a6c84a;
  --green:#2fa84f;
  --blue:#1f9fd9;
  --dark-grey:#5f5f5f;
  --navy:#1f2a63;
  --white:#ffffff;
  --stage:#eeeeee;
  --dieline:#e88a9a;
  --fold:#7fcf8a;
}
*{box-sizing:border-box;margin:0;padding:0}
html,body{width:1200px;height:540px;overflow:hidden}
body{background:var(--stage);font-family:"Raleway",sans-serif;position:relative}
.sheet{position:absolute;background:var(--white);box-shadow:0 1px 3px rgba(0,0,0,.25)}
.folder-outside{left:32px;top:38px;width:580px;height:464px}
.inside-sheet{left:634px;top:36px;width:536px;height:338px}

/* back panel test menu */
.test-menu{position:absolute;left:22px;top:0;width:266px;height:342px;background:var(--pink);padding:20px 20px 0 23px}
.menu-head{display:flex;justify-content:space-between;align-items:center;color:var(--white);height:9px}
.lab-name{font-size:7.5px;letter-spacing:2.6px;font-weight:500}
.menu-title{font-size:7.5px;font-weight:700;font-style:italic}
.menu-contact{display:flex;justify-content:space-between;color:var(--white);font-size:2.5px;margin-top:4px;height:4px}
.gene-table{position:absolute;left:23px;top:44px;width:223px;background:var(--white);font-size:3.5px}
.row{display:grid;grid-template-columns:95px 1fr;height:6.85px;align-items:center;padding-left:3px;white-space:nowrap;overflow:hidden}
.row:nth-child(even){background:var(--row-alt)}
.row .gene{color:var(--gene-red);font-weight:700}
.row .organs{color:#333}
.row.head{background:var(--red);color:var(--white);font-weight:600}
.row.group{grid-template-columns:1fr;color:var(--white);font-weight:600;padding-left:6px}
.group.lynch{background:var(--yellow)}
.group.peutz{background:var(--lime)}
.group.li{background:var(--green)}
.group.cowden{background:var(--blue)}
.group.gastric{background:var(--dark-grey)}
.row.lynch-row{background:var(--orange-row)}
.row.lynch-row:nth-child(odd){background:var(--pink-light)}

/* front cover */
.cover{position:absolute;left:288px;top:0;width:292px;height:338px;border-left:1px dashed var(--fold)}
.cover-band{position:absolute;left:2px;top:31px;width:268px;height:21px;background:var(--pink);color:var(--white);font-size:10px;letter-spacing:1.4px;text-align:center;line-height:21px}
.cover-tag{position:absolute;left:50px;top:73px;width:164px;height:13px;background:var(--grey);color:var(--white);font-size:5.8px;text-align:center;line-height:13px;letter-spacing:.3px;white-space:nowrap}
.ribbon{position:absolute;left:220px;top:72px}
.cover-lead{position:absolute;left:50px;top:89px;width:170px;font-size:5px;text-align:center;color:#444;line-height:1.4}
.cover-photo{position:absolute;left:2px;top:104px;width:268px;height:176px;background:linear-gradient(160deg,#e6e6e6,#a9a9a9 55%,#6f6f6f)}
.cover-foot{position:absolute;left:2px;top:284px;width:268px;height:18px;background:var(--grey);color:var(--white);font-size:6px;letter-spacing:.9px;text-align:center;line-height:18px}
.cover-mark{position:absolute;left:36px;top:296px;width:25px;height:25px;border-radius:50%;border:2px solid var(--navy);background:var(--white)}

/* pockets */
.pocket{position:absolute;top:338px;height:126px;border-top:1px solid var(--dieline)}
.pocket-left{left:22px;width:266px}
.pocket-right{left:288px;width:262px;border-left:1px solid var(--dieline)}
.glue-strip{position:absolute;top:0;width:17px;height:126px;background:var(--grey-light)}
.pocket-left .glue-strip{left:0}
.pocket-right .glue-strip{right:0}
.flip{position:absolute;transform:rotate(180deg);text-align:center;color:var(--navy);white-space:nowrap}
.pocket-left .flip{left:76px;top:9px;width:110px}
.pocket-right .flip{left:56px;top:32px;width:150px}
.brand-name{font-weight:700;font-size:8px}
.brand-sub{font-size:4.2px;margin-top:2px}
.brand-big{font-weight:700;font-size:11px;display:flex;align-items:center;justify-content:center;gap:5px}
.brand-dot{width:20px;height:20px;border-radius:50%;border:2px solid var(--navy);flex:none}
.slits{position:absolute;left:82px;top:32px}
.notch{position:absolute;width:12px;height:24px;border:1px solid var(--dieline);background:var(--stage)}
.notch.left{left:-1px;top:202px;border-left:none;border-radius:0 12px 12px 0}
.notch.right{right:-1px;top:202px;border-right:none;border-radius:12px 0 0 12px}

/* inside panels */
.inside-panel{position:absolute;top:12px;width:249px;height:318px;background:var(--pink)}
.panel-a{left:10px}
.panel-b{left:277px;color:var(--white);padding:28px 12px 0 33px}
.fold-line{position:absolute;left:267px;top:0;height:338px;border-left:1px dashed var(--fold)}
.body-copy{font-size:5.9px;line-height:1.22;text-align:justify;margin-bottom:5px}
.pull-quote{font-size:11px;line-height:1.3;text-align:center;margin:22px auto 0;width:184px}
</style>
</head>
<body>

<section class="sheet folder-outside">
  <span class="notch left"></span>
  <span class="notch right"></span>

  <div class="test-menu">
    <div class="menu-head">
      <span class="lab-name">QUILLBROOK LABS</span>
      <span class="menu-title">ORIVANE™ Test Menu</span>
    </div>
    <div class="menu-contact">
      <span>1480 Harbor Point Way, Suite 4 · Norwood, GA 30000 · 555 010 2040 · info@quillbrooklabs.example</span>
      <span>CLIA 00D0000000 · quillbrooklabs.example</span>
    </div>
    <div class="gene-table">
      <div class="row head"><span>GENE</span><span>CANCER-ASSOCIATED ORGAN SYSTEMS</span></div>
      <div class="row"><span class="gene">APC</span><span class="organs">Colon</span></div>
      <div class="row"><span class="gene">ATM</span><span class="organs">Breast/Pancreatic/Brain</span></div>
      <div class="row"><span class="gene">BARD1</span><span class="organs">Breast/Ovarian</span></div>
      <div class="row"><span class="gene">BMPR1A</span><span class="organs">Colon</span></div>
      <div class="row"><span class="gene">BRCA1</span><span class="organs">Breast/Ovarian/Prostate</span></div>
      <div class="row"><span class="gene">BRCA2</span><span class="organs">Breast/Ovarian/Prostate</span></div>
      <div class="row"><span class="gene">BRIP1</span><span class="organs">Breast/Ovarian</span></div>
      <div class="row"><span class="gene">CDK4</span><span class="organs">Melanoma</span></div>
      <div class="row"><span class="gene">P16 (CDKN2A)</span><span class="organs">Melanoma/Breast/Pancreatic/Squamous</span></div>
      <div class="row"><span class="gene">FANCC</span><span class="organs">Blood</span></div>
      <div class="row"><span class="gene">MEN1</span><span class="organs">Thyroid/Parathyroid</span></div>
      <div class="row"><span class="gene">MET</span><span class="organs">Renal/Hepatic</span></div>
      <div class="row"><span class="gene">MRE11A</span><span class="organs">Ovarian/Breast</span></div>
      <div class="row"><span class="gene">NBN</span><span class="organs">Breast/Ovarian/Prostate/Melanoma</span></div>
      <div class="row"><span class="gene">NF1</span><span class="organs">Blood</span></div>
      <div class="row"><span class="gene">NTRK1</span><span class="organs">Thyroid/Parathyroid</span></div>
      <div class="row"><span class="gene">PALB2</span><span class="organs">Breast/Ovarian/Pancreatic</span></div>
      <div class="row"><span class="gene">PTCH1</span><span class="organs">Melanoma/Brain/Breast/Colon</span></div>
      <div class="row"><span class="gene">RAD50</span><span class="organs">Breast/Ovarian</span></div>
      <div class="row"><span class="gene">RAD51C</span><span class="organs">Ovarian/Breast</span></div>
      <div class="row"><span class="gene">RAD51D</span><span class="organs">Ovarian/Breast</span></div>
      <div class="row"><span class="gene">RET</span><span class="organs">Lung/Thyroid/Parathyroid</span></div>
      <div class="row"><span class="gene">SMAD4</span><span class="organs">Colon/Pancreas</span></div>
      <div class="row group lynch">LYNCH SYNDROME GENES</div>
      <div class="row lynch-row"><span class="gene">MLH1</span><span class="organs">Colorectal/Ovarian</span></div>
      <div class="row lynch-row"><span class="gene">MSH2</span><span class="organs">Colorectal/Ovarian</span></div>
      <div class="row lynch-row"><span class="gene">MSH6</span><span class="organs">Colorectal/Ovarian</span></div>
      <div class="row lynch-row"><span class="gene">PMS2</span><span class="organs">Colorectal/Ovarian</span></div>
      <div class="row lynch-row"><span class="gene">EPCAM</span><span class="organs">Colorectal</span></div>
      <div class="row group peutz">PEUTZ-JEGHERS SYNDROME GENE</div>
      <div class="row"><span class="gene">STK11</span><span class="organs">Breast/Ovarian/Melanoma/Colorectal/Lung</span></div>
      <div class="row group li">LI-FRAUMENI SYNDROME GENE</div>
      <div class="row"><span class="gene">CHEK2</span><span class="organs">Breast/Ovarian/Prostate</span></div>
      <div class="row"><span class="gene">TP53</span><span class="organs">Breast/Bladder/Ovarian/Squamous</span></div>
      <div class="row group cowden">COWDEN SYNDROME GENE</div>
      <div class="row"><span class="gene">PTEN</span><span class="organs">Endometrium/Breast/Prostate/Lung</span></div>
      <div class="row group gastric">HEREDITARY DIFFUSE GASTRIC CANCER SYNDROME GENE</div>
      <div class="row"><span class="gene">CDH1</span><span class="organs">Breast/Gastric/Ovarian/Prostate</span></div>
      <div class="row"><span class="gene">VHL</span><span class="organs">Renal</span></div>
    </div>
  </div>

  <div class="cover">
    <div class="cover-band">HEREDITARY CANCER SCREENING</div>
    <div class="cover-tag">Doctors are the Gatekeepers to Genetic Testing</div>
    <svg class="ribbon" width="10" height="16" viewBox="0 0 10 16" aria-hidden="true">
      <path d="M5 1 C1 1 1 6 5 9 L1 15" fill="none" stroke="#f294a6" stroke-width="2"/>
      <path d="M5 1 C9 1 9 6 5 9 L9 15" fill="none" stroke="#5b9bd5" stroke-width="2"/>
    </svg>
    <p class="cover-lead">We have an obligation to help patients understand genetic risk and how testing can guide health care decisions.</p>
    <div class="cover-photo" role="img" aria-label="Black and white photograph of a multi-generation family sharing a meal at an outdoor table"></div>
    <div class="cover-foot">The test you order FOR your patients</div>
    <span class="cover-mark" aria-hidden="true"></span>
  </div>

  <div class="pocket pocket-left">
    <span class="glue-strip"></span>
    <div class="flip">
      <div class="brand-name">Celvara Health Group</div>
      <div class="brand-sub">a division of Meridian Clinical Sales LLC</div>
    </div>
    <svg class="slits" width="104" height="60" viewBox="0 0 104 60" aria-hidden="true">
      <g stroke="#e8393a" stroke-width=".8">
        <line x1="2" y1="16" x2="16" y2="2"/><line x1="88" y1="2" x2="102" y2="16"/>
        <line x1="2" y1="44" x2="16" y2="58"/><line x1="88" y1="58" x2="102" y2="44"/>
      </g>
    </svg>
  </div>

  <div class="pocket pocket-right">
    <span class="glue-strip"></span>
    <div class="flip">
      <div class="brand-big"><span class="brand-dot"></span><span>Celvara Health Group</span></div>
      <div class="brand-sub">a division of Meridian Clinical Sales LLC</div>
    </div>
  </div>
</section>

<section class="sheet inside-sheet">
  <div class="inside-panel panel-a"></div>
  <span class="fold-line"></span>
  <div class="inside-panel panel-b">
    <p class="body-copy">There are many benefits to getting tested, regardless of the eventual result. If one of your family members — however distant — had cancer, there is a chance that you inherited a gene mutation that not only increases your personal risk of cancer, but also could be passed to the next generation. Those who are carriers of hereditary cancer gene mutations, could be at risk of getting cancer earlier in life than the general population. The sooner genetic testing is done, the more likely it is that the risk can be managed appropriately.</p>
    <p class="body-copy">Hereditary cancer screening provides vital information to help people with a strong personal or family history of cancer understand their own risk of developing the disease. With this information, they can take steps to Potentially Prevent Cancer, Delay the Onset of Cancer or Catch it at an Earlier stage when outcomes and survival rates are Better.</p>
    <p class="pull-quote">Identifying an inherited genetic mutation has the potential to prevent cancer and save lives.</p>
  </div>
</section>

</body>
</html>
```